Business Card for Multi-Brand Sportswear Company

We are looking for a business card which represents our company and the multiple brands within it.

The company: Fen Athletics (LTD)
The brands: Fen, TavaPuni, ElmStretch, Grit and Rain

Employees using these cards would be representing Fen Athletics, rather than any of the individual brands. You will see a current design within the uploaded files, to give some inspiration. The actual text of the brands is not necessary, but the logos should be on there is some format.

Our creative minds on this are stretched, so we are looking for someone to make this their own, and show us what a good business card should look like.

We may like to get these printed with spot gloss, so keep that in mind with your designs.

www.fenathletics.co.uk

Industry/Entity Type

Business

Contact Information for Business Card

Leo Pemberton-Hale
Operations Manager
(+44) 1632 960 418
Leo@fenathletics.co.uk
www.fenathletics.co.uk

Font styles to use
Sans Serif
Other font styles liked:
• Eurostile

Colors
ffffff

Requirements
Nice to have
• Dark (black) background

```html
<!DOCTYPE html>
<html lang="en">
<head>
<meta charset="utf-8">
<title>Fen Athletics — Business Card</title>
<link rel="stylesheet" href="https://fonts.googleapis.com/css2?family=Open+Sans:ital,wght@0,400;0,600;1,400;1,700&display=swap">
<style>
  :root {
    --stage: #d9d9dc;
    --card: #222222;
    --brand-red: #e8242b;
    --ink-white: #ffffff;
    --icon-dark: #222222;
  }
  * { margin: 0; padding: 0; box-sizing: border-box; }
  html, body { width: 1200px; height: 1000px; overflow: hidden; }
  body {
    background: var(--stage);
    font-family: "Open Sans", Arial, sans-serif;
    position: relative;
  }
  .card {
    position: absolute;
    top: 170px;
    width: 398px;
    height: 665px;
    background: var(--card);
    overflow: hidden;
  }
  .card--front { left: 171px; }
  .card--back { left: 630px; }

  .brand-band { position: absolute; left: 0; top: 62px; }
  .brand-band__name {
    position: absolute;
    left: 48px;
    top: 74px;
    color: var(--ink-white);
    font-weight: 600;
    font-size: 21px;
    letter-spacing: 0.5px;
    text-transform: uppercase;
    white-space: nowrap;
  }

  .holder { position: absolute; left: 50px; top: 197px; }
  .holder__name {
    color: var(--ink-white);
    font-style: italic;
    font-weight: 700;
    font-size: 19px;
    letter-spacing: 0.3px;
    text-transform: uppercase;
  }
  .holder__role {
    color: var(--brand-red);
    font-style: italic;
    font-size: 16px;
    margin-top: 1px;
  }

  .contact-list { position: absolute; left: 42px; top: 280px; list-style: none; }
  .contact-list__item {
    display: flex;
    align-items: center;
    height: 30.5px;
    color: var(--ink-white);
    font-style: italic;
    font-size: 16px;
  }
  .contact-list__icon { width: 32px; height: 18px; margin-right: 4px; flex: none; }

  .brand-row {
    position: absolute;
    left: 0; right: 0;
    top: 572px;
    display: flex;
    justify-content: center;
    gap: 18px;
    padding-left: 20px;
  }
  .brand-row__name {
    color: var(--brand-red);
    font-size: 11px;
    font-weight: 600;
    white-space: nowrap;
  }

  .back-mark {
    position: absolute;
    left: 0; right: 0;
    top: 330px;
    text-align: center;
    color: var(--ink-white);
    font-weight: 600;
    font-size: 30px;
    letter-spacing: 2px;
    text-transform: uppercase;
  }
</style>
</head>
<body>
  <section class="card card--front" aria-label="Business card front">
    <svg class="brand-band" width="398" height="56" viewBox="0 0 398 56" aria-hidden="true">
      <polygon points="0,0 55,0 3,54 0,54" fill="var(--brand-red)"/>
      <polygon points="62,0 366,0 314,54 10,54" fill="var(--brand-red)"/>
    </svg>
    <div class="brand-band__name">Fen Athletics</div>

    <div class="holder">
      <div class="holder__name">Leo Pemberton-Hale</div>
      <div class="holder__role">Operations Manager</div>
    </div>

    <ul class="contact-list">
      <li class="contact-list__item">
        <svg class="contact-list__icon" viewBox="0 0 32 18" aria-hidden="true">
          <polygon points="8,0 32,0 24,18 0,18" fill="var(--brand-red)"/>
          <path d="M10 12 h12 v2 h-12z M12 7 q4 -4 8 0 v3 h-8z" fill="var(--icon-dark)"/>
        </svg>
        (+44) 1632 960 418
      </li>
      <li class="contact-list__item">
        <svg class="contact-list__icon" viewBox="0 0 32 18" aria-hidden="true">
          <polygon points="8,0 32,0 24,18 0,18" fill="var(--brand-red)"/>
          <rect x="10" y="5" width="12" height="8" fill="none" stroke="var(--icon-dark)" stroke-width="1.5"/>
          <path d="M10 5 l6 5 l6 -5" fill="none" stroke="var(--icon-dark)" stroke-width="1.5"/>
        </svg>
        Leo@fenathletics.co.uk
      </li>
      <li class="contact-list__item">
        <svg class="contact-list__icon" viewBox="0 0 32 18" aria-hidden="true">
          <polygon points="8,0 32,0 24,18 0,18" fill="var(--brand-red)"/>
          <circle cx="16" cy="9" r="5" fill="none" stroke="var(--icon-dark)" stroke-width="1.5"/>
          <path d="M11 9 h10 M16 4 v10" stroke="var(--icon-dark)" stroke-width="1.2"/>
        </svg>
        www.fenathletics.co.uk
      </li>
    </ul>

    <div class="brand-row">
      <span class="brand-row__name">TavaPuni</span>
      <span class="brand-row__name">ElmStretch</span>
      <span class="brand-row__name">Grit and Rain</span>
    </div>
  </section>

  <section class="card card--back" aria-label="Business card back">
    <div class="back-mark">Fen</div>
  </section>
</body>
</html>
```